New webdesign for a cable company

We need a new design for Lunor Media.

There exist a suggestion for the page, were we have attached files to show you this. The design here is not good enough, but here you can se what content we need.

You can feel free to give adjustment to this design to make it better, our blow us away with a new brilliant design, but from this design you see what content we need.

The important is that the company get a design who represent its products:
- TV = Cable TV
- Bredbånd = Broadband
- Mobil = Mobile phone
- Strøm = Electricity
- Alarm = Alarm
- Lunor Komplett = a cobain pagage of all our products.

Lunor Media would like costumers who visit the site to het the impression that Lunor Media is a professional, innovative and fun company.
Updates

We have to day uploaded pictures of the existing page as the link haven't been working for the most of you as it's placed on a server our developer are using and is often shut it down. 

We have also updated the brief with some new and updated description so please read true the updated brief. 

We will at the same time inform that we haven't been able to give feedback on any of the received design and are sorry for that, we will within the next 24 hours hopefully have started responded the different received designs.

Looking forward to see more suggestion and hope you will help us create and very professional and informative design. 

Reason: We have decided to extend the deadline due to the number of design suggestion who is sent in and your lack of response to all designers due to our own workload.

This project was unfortunately for different reason put on ice for a while, but we are now ready to complete the design and will answer and give feedback too all the received design suggestions. 

Within a couple of days we hope we have answered all you who sent us suggestions, we appreciate all suggestions and hope to get in more suggestions.

Reason: Deisgn description have been updated

Target Market(s)

Our costumer are both private and companies

Industry/Entity Type

Tv

Requirements
Must have
• A easy way to promote and inform about changes in our products, there are a constant change in our products and it must bee a easy and good way to changes ass the marked change. Cheek out this link, for a example of what we like/think of here, https://nett.fjordsignal.no

On all pages there must be a easy way to click on a order button and too inform about your interest (thats two different things), could be placed in the top right corner for example. In the order form you should follow a step by step part:
1. Cheek what product we can provide you.
2. Chooce products.
3. Costumer inforamtion.
4. Confirmation.

Somewere on the portal it must be possible for costumers to log on to their own administration, where they can cheek for invoices, other statuses, etc.

A main menu existing of:
Hjem (Home)
Produkter (Products)
Storkunde (key account/large costumers)
Kundeservice (Costumerservice)
Min side (My page)

The main menu should have the following sub titles:
- Under "Produkter"/products our different products must be listed
- Under "Kundeservice"/Costumerservice it must have these submenus:
- Hjelp og støtte = Help.
- Faktura = Invoice
- Brukerguider = Userguides
- Abbonementavtaler = Terms and conditions.

A bottom menu where we have 5 main categories, with sub categories:
Om oss (about us)
- Om Lunor Media (about Lunor Media)
- Kontaktinformajson ( contact information)
- Pressemeldinger (Pressrelese)
- Ledige stillinger (positions available)
- KRAV ( and organisastion in our field)

Produkter (Product)
- TV (TV)
- Bredbånd (Broadand)
- Telefoni (telephony, both mobil)
- Strøm (elecricity)
- Arlam (Alarm)

Borrettslag/Sameier (Housing cooperatives)
- Løsninger (solutions)
- Produkter (product)
- Kontaktpersoner (contactpersons)

Utbygger (developer)
- Hva vi kan gjøre for dere. (What we can do for you)

Opperatørnett (operators)

Build up the categories and bottom menu something like this:
https://nett.fjordsignal.no
www.brevix.com
Nice to have
• A main menu existing of:
Hjem (Home)
Produkter (Products)
Lunor Media
Kontakt oss (Contact us)

Under "Produkter"/products our different products must be listed and under "Kundeservice"/Costumerservice it must have these submenus:
- Hjelp og støtte = Help.
- Faktura = Invoice
Should not have
• Any translation section since the homepage only will be in Norwegian.

```html
<!DOCTYPE html>
<html lang="no">
<head>
<meta charset="utf-8">
<title>Lunor Media – Mobile Phones</title>
<link href="https://fonts.googleapis.com/css2?family=Raleway:wght@300;400;600;700;800&family=Montserrat:wght@700&family=Roboto+Condensed:ital,wght@1,400&display=swap" rel="stylesheet">
<style>
:root{
  --blue:#1ba6dd;
  --blue-dark:#1686b8;
  --green:#5aa51a;
  --price:#4a9a12;
  --ink:#222;
  --footer:#0f1011;
  --panel:#f6f6f6;
  --page:#e9e9e9;
  --muted:#8f9296;
  --link:#a4a7ab;
}
*{margin:0;padding:0;box-sizing:border-box}
html,body{width:804px;height:1200px;overflow:hidden}
body{position:relative;background:var(--page);font-family:"Raleway",sans-serif;color:var(--ink)}
.abs{position:absolute}
a{text-decoration:none;color:inherit}

.site-header{left:0;top:0;width:804px;height:68px;background:#fff}
.brand{left:134px;top:24px;display:flex;align-items:center;gap:7px;font-size:22px;font-weight:400;color:#2b8fc4}
.brand i{display:block;width:20px;height:20px;border-radius:50%;background:#2b8fc4}
.cta{top:0;height:18px;display:flex;align-items:center;gap:4px;padding:0 7px;color:#fff;font-size:8px;font-weight:700;letter-spacing:-.3px;white-space:nowrap}
.cta.order{left:448px;width:110px;background:var(--green)}
.cta.interest{left:558px;width:112px;background:var(--blue)}
.cta .dot{width:9px;height:9px;border-radius:50%;background:#fff;flex:none}
.social{top:31px;left:621px;display:flex;gap:3px}
.social i{width:15px;height:15px;border-radius:50%;background:#3aa7de}
.social i:nth-child(2){background:#2f5ca8}
.social i:nth-child(3){background:#3a3a3a}
.main-nav{left:346px;top:52px;display:flex;font-size:8.5px;font-weight:700;color:#333;white-space:nowrap}
.main-nav a{padding:0 8px;border-left:1px solid #bbb;line-height:10px;position:relative}
.main-nav a:first-child{border:0}
.main-nav a.active:after{content:"";position:absolute;left:0;right:0;top:14px;height:3px;background:var(--blue)}

.hero{left:0;top:68px;width:804px;height:192px;background:linear-gradient(#2a2d31,#1d1f22)}
.hero-media{left:164px;top:12px;width:188px;height:146px;border-radius:6px;background:linear-gradient(120deg,#3c3c3c 0%,#4e4e4e 48%,#e8e8e8 49%,#dcdcdc 58%,#2a6fc4 59%,#1e5aa8 78%,#e4e4e4 79%)}
.hero h1{left:394px;top:20px;font-size:29px;font-weight:800;color:#fff;letter-spacing:-.5px}
.hero ul{left:394px;top:55px;list-style:none;color:#e8e8e8;font-size:13px;font-weight:300;letter-spacing:-.6px;white-space:nowrap}
.hero li{height:17.3px;display:flex;align-items:center;gap:6px}
.hero li svg{flex:none}
.btn-more{left:394px;top:134px;width:61px;height:16px;background:var(--blue);color:#fff;font-size:7px;font-weight:700;display:flex;align-items:center;justify-content:center}

.products{left:134px;top:236px;width:536px;height:678px;background:var(--panel);box-shadow:0 2px 8px rgba(0,0,0,.12)}
.products h2{left:16px;top:14px;font-size:18px;font-weight:800;color:var(--blue);letter-spacing:-.4px}
.card{width:122px;height:142px;background:#fafafa;border:1px solid #dedede;border-bottom:0}
.card .shot{position:absolute;left:30px;top:12px;width:62px;height:76px;border-radius:6px}
.shot.phone{background:linear-gradient(160deg,#e2e4e6,#c9ced4)}
.shot.cam{background:linear-gradient(160deg,#6b6e72,#2c2e31)}
.shot.pump{background:linear-gradient(160deg,#4a7fd6,#1d4ea8)}
.shot.tool{background:linear-gradient(160deg,#7fb2ef,#3a7fd8)}
.shot.meter{background:linear-gradient(160deg,#9aa6bb,#4d5870)}
.card .price{position:absolute;left:0;right:0;top:97px;text-align:center;font-size:14px;font-weight:600;color:var(--price)}
.card .bar{position:absolute;left:-1px;right:-1px;top:123px;height:19px;background:#141414;color:#fff;font-family:"Montserrat",sans-serif;font-size:7.6px;font-weight:700;display:flex;align-items:center;padding-left:6px}
.card .bar:after{content:"";position:absolute;right:6px;top:6.5px;border-left:5px solid #fff;border-top:3px solid transparent;border-bottom:3px solid transparent}

.pager{left:311px;top:885px;display:flex;gap:5px}
.pager span{height:13px;min-width:13px;border:1px solid #c8c8c8;border-radius:3px;background:#f2f2f2;font-size:6.5px;color:#666;display:flex;align-items:center;justify-content:center}
.pager span.wide{min-width:22px;font-size:9px}
.pager span.on{background:#666;color:#fff;border-color:#555}

.services{left:134px;top:938px;width:536px;height:24px;display:flex;align-items:center;gap:10px}
.services:before,.services:after{content:"";flex:1;height:1px;background:#d4d4d4}
.services h3{font-family:"Roboto Condensed",sans-serif;font-style:italic;font-weight:400;font-size:21px;letter-spacing:-1.3px;color:var(--green)}

.finder{left:0;top:974px;width:804px;height:34px;background:linear-gradient(#27b1e6,var(--blue-dark))}
.field{top:10px;height:18px;background:#fff;border-radius:2px;display:flex;align-items:center;gap:6px;padding-left:5px;font-size:7px;color:#b5b5b5}
.field i{width:11px;height:8px;background:#7cc8ea;border-radius:1px}
.field.addr{left:137px;width:231px}
.field.tel{left:374px;width:232px}
.btn-find{left:612px;top:10px;width:58px;height:18px;background:#101010;color:#fff;font-size:8px;font-weight:700;letter-spacing:-.3px;display:flex;align-items:center;justify-content:center;border-radius:2px}

.site-footer{left:0;top:1008px;width:804px;height:192px;background:var(--footer);color:var(--muted)}
.fcol{color:var(--link)}
.fcol h4{font-size:12px;font-weight:600;color:#e6e6e6;letter-spacing:-.4px;padding-bottom:3px;border-bottom:1px dotted #6a6a6a;margin-bottom:5px;white-space:nowrap}
.fcol p{font-size:8.5px;font-weight:300;letter-spacing:-.3px;line-height:14.6px;white-space:nowrap}
.flogo{left:540px;top:1117px;display:flex;align-items:center;gap:6px;font-size:20px;font-weight:400;color:#fff}
.flogo i{width:18px;height:18px;border-radius:50%;background:#fff}
.terms{left:137px;top:1139px;font-size:7.5px;font-weight:300;letter-spacing:-.3px;color:var(--muted)}
.footer-rule{left:0;top:1154px;width:804px;height:1px;background:#2a2a2a}
.legal{left:137px;top:1164px;width:540px;font-size:7.5px;font-weight:300;line-height:13px;letter-spacing:-.2px;color:var(--muted)}
</style>
</head>
<body>

<header class="abs site-header">
  <div class="abs brand"><i></i>Lunor Media</div>
  <a class="abs cta order"><span class="dot"></span>BLI KUNDE I DAG</a>
  <a class="abs cta interest"><span class="dot"></span>MELD DIN INTERESSE</a>
  <div class="abs social"><i></i><i></i><i></i></div>
  <nav class="abs main-nav">
    <a class="active">Hjem</a><a>Produkter</a><a>Storkunde</a><a>Kundeservice</a><a>Min Side</a><a>Kontakt Oss</a>
  </nav>
</header>

<section class="abs hero">
  <div class="abs hero-media" role="img" aria-label="Two smartphones, one shown from the back and one from the front with a tile home screen"></div>
  <h1 class="abs">MOBILE PHONES</h1>
  <ul class="abs">
    <li><svg width="14" height="8" viewBox="0 0 14 8"><path d="M0 4h2M4 4h2M8 4h3" stroke="#1ba6dd" stroke-width="1.6"/><path d="M10 1l3 3-3 3" fill="none" stroke="#1ba6dd" stroke-width="1.6"/></svg>Cheek What Product We Can Provide You.</li>
    <li><svg width="14" height="8" viewBox="0 0 14 8"><path d="M0 4h2M4 4h2M8 4h3" stroke="#1ba6dd" stroke-width="1.6"/><path d="M10 1l3 3-3 3" fill="none" stroke="#1ba6dd" stroke-width="1.6"/></svg>Chooce Products.</li>
    <li><svg width="14" height="8" viewBox="0 0 14 8"><path d="M0 4h2M4 4h2M8 4h3" stroke="#1ba6dd" stroke-width="1.6"/><path d="M10 1l3 3-3 3" fill="none" stroke="#1ba6dd" stroke-width="1.6"/></svg>Costumer Inforamtion.</li>
    <li><svg width="14" height="8" viewBox="0 0 14 8"><path d="M0 4h2M4 4h2M8 4h3" stroke="#1ba6dd" stroke-width="1.6"/><path d="M10 1l3 3-3 3" fill="none" stroke="#1ba6dd" stroke-width="1.6"/></svg>Confirmation.</li>
  </ul>
  <a class="abs btn-more">READ MORE</a>
</section>

<main class="abs products">
  <h2 class="abs">OUR PRODUCTS</h2>

  <div class="abs card" style="left:16px;top:46px"><div class="shot phone" role="img" aria-label="Smartphone"></div><div class="price">$ 450.00</div><div class="bar">LOREM IPSUM DOLOR</div></div>
  <div class="abs card" style="left:144px;top:46px"><div class="shot cam" role="img" aria-label="Dashboard camera"></div><div class="price">$ 200.00</div><div class="bar">LOREM IPSUM DOLOR</div></div>
  <div class="abs card" style="left:271px;top:46px"><div class="shot pump" role="img" aria-label="Portable air compressor"></div><div class="price">$ 350.00</div><div class="bar">LOREM IPSUM DOLOR</div></div>
  <div class="abs card" style="left:399px;top:46px"><div class="shot tool" role="img" aria-label="Blue handheld tool"></div><div class="price">$ 120.00</div><div class="bar">LOREM IPSUM DOLOR</div></div>

  <div class="abs card" style="left:16px;top:194px"><div class="shot cam" role="img" aria-label="Dashboard camera"></div><div class="price">$ 675.00</div><div class="bar">LOREM IPSUM DOLOR</div></div>
  <div class="abs card" style="left:144px;top:194px"><div class="shot meter" role="img" aria-label="Handheld digital meter"></div><div class="price">$ 700.00</div><div class="bar">LOREM IPSUM DOLOR</div></div>
  <div class="abs card" style="left:271px;top:194px"><div class="shot phone" role="img" aria-label="Smartphone"></div><div class="price">$370.00</div><div class="bar">LOREM IPSUM DOLOR</div></div>
  <div class="abs card" style="left:399px;top:194px"><div class="shot pump" role="img" aria-label="Portable air compressor"></div><div class="price">$ 500.00</div><div class="bar">LOREM IPSUM DOLOR</div></div>

  <div class="abs card" style="left:16px;top:342px"><div class="shot meter" role="img" aria-label="Handheld digital meter"></div><div class="price">$ 450.00</div><div class="bar">LOREM IPSUM DOLOR</div></div>
  <div class="abs card" style="left:144px;top:342px"><div class="shot tool" role="img" aria-label="Blue handheld tool"></div><div class="price">$ 350.00</div><div class="bar">LOREM IPSUM DOLOR</div></div>
  <div class="abs card" style="left:271px;top:342px"><div class="shot phone" role="img" aria-label="Smartphone"></div><div class="price">$ 950.00</div><div class="bar">LOREM IPSUM DOLOR</div></div>
  <div class="abs card" style="left:399px;top:342px"><div class="shot cam" role="img" aria-label="Dashboard camera"></div><div class="price">$ 450.00</div><div class="bar">LOREM IPSUM DOLOR</div></div>

  <div class="abs card" style="left:16px;top:490px"><div class="shot cam" role="img" aria-label="Dashboard camera"></div><div class="price">$ 450.00</div><div class="bar">LOREM IPSUM DOLOR</div></div>
  <div class="abs card" style="left:144px;top:490px"><div class="shot pump" role="img" aria-label="Portable air compressor"></div><div class="price">$ 350.00</div><div class="bar">LOREM IPSUM DOLOR</div></div>
  <div class="abs card" style="left:271px;top:490px"><div class="shot meter" role="img" aria-label="Handheld digital meter"></div><div class="price">$ 950.00</div><div class="bar">LOREM IPSUM DOLOR</div></div>
  <div class="abs card" style="left:399px;top:490px"><div class="shot phone" role="img" aria-label="Smartphone"></div><div class="price">$ 450.00</div><div class="bar">LOREM IPSUM DOLOR</div></div>
</main>

<nav class="abs pager">
  <span class="wide">«</span><span>1</span><span>2</span><span class="on">3</span><span>4</span><span>7</span><span>8</span><span>9</span><span class="wide">»</span>
</nav>

<div class="abs services"><h3>Hvilke tjenester kan vi tilby deg</h3></div>

<section class="abs finder">
  <div class="abs field addr"><i></i>Addresse</div>
  <div class="abs field tel"><i></i>Telefonnummer</div>
  <a class="abs btn-find">FIND NOW</a>
</section>

<footer class="abs site-footer"></footer>
<div class="abs fcol" style="left:137px;top:1027px;width:80px"><h4>Om Oss</h4><p>Om Lunor Media<br>Kontaktinformasjon<br>Pressemeldinger<br>Ledige stillinger<br>KRAV</p></div>
<div class="abs fcol" style="left:255px;top:1027px;width:72px"><h4>Produkter</h4><p>TV<br>Bredbånd<br>Telefoni<br>Strøm<br>Arlam</p></div>
<div class="abs fcol" style="left:357px;top:1027px;width:128px"><h4>Borrettslag/Sameier</h4><p>Løsninger<br>Produkter<br>Kontaktpersoner</p></div>
<div class="abs fcol" style="left:542px;top:1026px;width:128px"><h4>Utbygger</h4><p>Hva vi kan gjøre for dere.</p></div>
<div class="abs fcol" style="left:542px;top:1067px;width:128px"><h4>Opperatørnett</h4><p>Hva vi kan gjøre for dere</p></div>
<div class="abs flogo"><i></i>Lunor Media</div>
<div class="abs terms">Ordinære vilkår Lunor Media Kabel-TV Personinformasjon og cookies</div>
<div class="abs footer-rule"></div>
<p class="abs legal">Lunor Media Nordens største TV-distributør og Norges nest største bredbåndsleverandør. Vår virksomhet består av to enheter; Lunor Media Kabel-TV AS og Lunor Media Norge AS Copyright © 2013 Lunor Media.</p>

</body>
</html>
```